Equipment Finance Specialist I work with companies who need the funds to buy their equipment

I would like a business card that stands out on the shelves. I want to be able to hand it to someone and say WOW. This card should have my logo.
You can put color into it I am very open on design and color

What my company does is we deal with dealerships that sell equipment such as Dump Trucks garbage trucks tractors trailers. Customers get referred to us and depending on their time in business we will ask for the following items

Companies that have been in business for more than two years we have a credit application program up to 250K . With this program we need the following items Credit application filled out(which is what I would like to be able for the customer to click on my website to get.) as well as three current month bank statements.

Deals over 250k we will need the following items

2 years business tax returns
2 years personal tax returns
Profit & Loss statement
Personal Financial Statement

what we do
100% FINANCING
SEASONAL PAYMENTS
LOAN BALLOON PAYMENTS
TRAC LEASING
LOW-INTEREST REFINANCING RATES
DEBT CONSOLIDATION

We specialize in creative financing solutions and offer a variety of reliable, flexible and expandable lending choices.

Target Market(s)

Trucking Companies

Industry/Entity Type

Trucking Company

Contact Information for Business Card

* $250,000 Application only Program
* Loans from $30,000 to 5,000,000
* Competitive Interest Rates

Font styles to use
Serif
Sans Serif

Colors

Designer to choose colors to be used in the design.

Requirements
Must have
• On the back of the card.
• * $250,000 Application only Program
• * Loans from $30,000 to 5,000,000
• My name, email, website. address
• * Competitive Interest Rates
• * 100% Financing
Nice to have
• I want my logo to pop on the card
• My logo is the great one I would like to use
Should not have
• I am up for your creativity as well

```html
<!DOCTYPE html>
<html lang="en">
<head>
<meta charset="utf-8">
<title>Summit Lending — Business Card</title>
<link rel="stylesheet" href="https://fonts.googleapis.com/css2?family=Mulish:wght@400;600;800&display=swap">
<style>
  :root {
    --navy: #1b2a63;
    --navy-deep: #15214f;
    --red: #e21f35;
    --paper: #ffffff;
    --paper-shade: #eceef1;
    --stage: #3a3c40;
    --silver: #e4e6ea;
  }
  * { box-sizing: border-box; margin: 0; padding: 0; }
  html, body { width: 1200px; height: 900px; overflow: hidden; }
  body {
    background: var(--stage);
    font-family: "Mulish", sans-serif;
    display: flex;
    flex-direction: column;
    align-items: center;
    justify-content: space-evenly;
  }
  .card {
    position: relative;
    width: 700px;
    height: 400px;
    border-radius: 18px;
    overflow: hidden;
  }

  /* Front */
  .card--front {
    background: linear-gradient(135deg, var(--paper-shade) 0%, var(--paper) 55%);
  }
  .brand {
    position: absolute;
    left: 50px;
    top: 120px;
    width: 260px;
    display: flex;
    align-items: center;
    gap: 16px;
  }
  .brand__dot {
    width: 52px; height: 52px;
    border-radius: 50%;
    background: var(--navy);
    flex: none;
  }
  .brand__name {
    font-weight: 800;
    font-size: 36px;
    letter-spacing: 1px;
    text-transform: uppercase;
    color: var(--navy);
    line-height: 1.05;
  }
  .divider {
    position: absolute;
    left: 335px;
    top: 80px;
    width: 2px;
    height: 225px;
    background: var(--navy);
  }
  .contact {
    position: absolute;
    left: 368px;
    top: 82px;
    color: var(--navy);
  }
  .contact__name {
    font-weight: 600;
    font-size: 27px;
    line-height: 1.2;
    color: var(--red);
    letter-spacing: 1px;
    text-transform: uppercase;
  }
  .contact__role { font-size: 17px; line-height: 1.3; margin-top: 4px; }
  .contact__address { font-size: 17px; line-height: 1.35; margin-top: 16px; }
  .contact__list { list-style: none; margin-top: 14px; font-size: 17px; line-height: 1.5; }
  .contact__list li { display: flex; align-items: center; gap: 10px; }
  .contact__list svg { width: 13px; height: 13px; fill: none; stroke: var(--red); stroke-width: 2; flex: none; }
  .contact__web-accent { color: var(--red); }
  .edge {
    position: absolute;
    left: 0; right: 0; bottom: 0;
    height: 12px;
    display: flex;
  }
  .edge__red { width: 42%; background: var(--red); }
  .edge__navy { flex: 1; background: var(--navy); }

  /* Back */
  .card--back {
    background: linear-gradient(135deg, var(--navy) 0%, var(--navy-deep) 100%);
    display: flex;
    flex-direction: column;
    align-items: center;
    justify-content: center;
    gap: 34px;
  }
  .back-brand {
    display: flex;
    align-items: center;
    gap: 22px;
  }
  .back-brand .brand__dot { width: 64px; height: 64px; background: var(--silver); }
  .back-brand .brand__name { font-size: 50px; color: var(--silver); }
  .programs {
    list-style: none;
    display: grid;
    grid-template-columns: auto auto;
    column-gap: 40px;
    row-gap: 12px;
    color: var(--silver);
    font-size: 17px;
    font-weight: 600;
  }
  .programs li { display: flex; align-items: center; gap: 10px; }
  .programs li::before {
    content: "";
    width: 8px; height: 8px;
    background: var(--red);
    flex: none;
  }
</style>
</head>
<body>
  <section class="card card--front" aria-label="Business card front">
    <div class="brand">
      <span class="brand__dot"></span>
      <span class="brand__name">Summit<br>Lending</span>
    </div>
    <div class="divider"></div>
    <div class="contact">
      <p class="contact__name">Daniel Reyes</p>
      <p class="contact__role">Director</p>
      <p class="contact__address">1820 Harbor Ridge Dr.<br>Austin, TX 78701</p>
      <ul class="contact__list">
        <li>
          <svg viewBox="0 0 16 16"><path d="M4 2l3 3-2 2c1 2 2 3 4 4l2-2 3 3-2 2C7 14 2 9 2 4z"/></svg>
          1300 555 014
        </li>
        <li>
          <svg viewBox="0 0 16 16"><rect x="1.5" y="3.5" width="13" height="9"/><path d="M1.5 3.5l6.5 5 6.5-5"/></svg>
          info@summitlending.com
        </li>
        <li>
          <svg viewBox="0 0 16 16"><circle cx="8" cy="8" r="6.5"/><path d="M1.5 8h13M8 1.5c-3 3.5-3 9.5 0 13M8 1.5c3 3.5 3 9.5 0 13"/></svg>
          <span>www.<span class="contact__web-accent">summitlending</span>.com</span>
        </li>
      </ul>
    </div>
    <div class="edge"><span class="edge__red"></span><span class="edge__navy"></span></div>
  </section>

  <section class="card card--back" aria-label="Business card back">
    <div class="back-brand">
      <span class="brand__dot"></span>
      <span class="brand__name">Summit Lending</span>
    </div>
    <ul class="programs">
      <li>$250,000 Application Only Program</li>
      <li>Loans from $30,000 to $5,000,000</li>
      <li>Competitive Interest Rates</li>
      <li>100% Financing</li>
    </ul>
  </section>
</body>
</html>
```